Brisk. Technology Logistics Software platform.

A modern looking and feeling website for a logistics software platform.
We connect retailers or wholesale parcel distributors to worldwide delivery solutions.
Methods tend to be road and air transport to final mile courier companies and post offices all over the world.
Our platform is for ecommerce distribution. A customer uses BRISK to enable them to connect to worldwide companies who will track and trace the delivery of their goods.

Target Market(s)

Onllne retailers. Markert Places such as Vendora and Tradelo. Wholesale third party logistics and packaging companies. Delivery companies based in the UK looking to expand overseas.

Number of Pages Required

5+ page

Font styles to use
Sans Serif

Colors
aaaaaa
dbdbdb
e6e6e6
c4c4c4
cbcbcb
c9c9c9
ec1f27
3176b5
0355a3

Requirements
Must have
• Landing Page.
• What we do.
• Who we are.
• Modules.
• Testimonies (password protected)
• Contact us.
• Interactive for mobile operating systems.
• Scrolling website.
• Short stock video showing on key pages.
• Very well polished fonts and buttons. A sharp and well executed website is required.
• Simplicity in feeling.
• To the point on message.
• Refined wording and copyrighting / messaging
• A link to our sub brand and product Brisk Parcels
• Capture interest so people read further.
Nice to have
• A polished video to explain what we do on landing page. Clipmarrow.net have some good options but not sure how professional they will look.
Should not have
• Bad graphics and colours.
• Not lots of clicks. Less as possible
• Complex message

```html
<!DOCTYPE html>
<html lang="en">
<head>
<meta charset="utf-8">
<title>Brisk. Technology – Web Design</title>
<link href="https://fonts.googleapis.com/css2?family=Fira+Sans:wght@400;500;600&family=Lato:wght@400;700&display=swap" rel="stylesheet">
<style>
:root{
  --stage:#000000;
  --white:#ffffff;
  --brand-red:#ec1f27;
  --brand-blue:#0355a3;
  --brand-blue-light:#3176b5;
  --ink:#1d1d1d;
  --footer-grey:#9a9a9a;
  --rule:#c4c4c4;
  --hero-dark:#0b2a52;
  --hero-mid:#1a5283;
}
*{margin:0;padding:0;box-sizing:border-box}
html,body{width:1200px;height:557px;overflow:hidden;background:var(--stage)}
.stage{position:relative;width:1200px;height:557px;background:var(--stage)}

/* Landing screen */
.landing{position:absolute;left:19px;top:124px;width:557px;height:315px;overflow:hidden;font-family:"Fira Sans",sans-serif;color:var(--white)}
.landing-backdrop{position:absolute;inset:0;background:radial-gradient(ellipse at 75% 20%,#5a6e84 0%,#34414f 35%,#1f262d 70%,#15191d 100%)}
.landing-shade{position:absolute;inset:0;background:rgba(0,0,0,.35)}
.landing-brand{position:absolute;left:0;right:0;top:33px;text-align:center;font-size:22px;font-weight:600;letter-spacing:.5px}
.landing-brand .brand-dot{display:inline-block;width:10px;height:10px;background:var(--brand-red);border-radius:50%;margin-right:5px;vertical-align:2px}
.landing-title{position:absolute;left:0;right:0;top:94px;text-align:center;font-size:15.5px;font-weight:500}
.landing-copy{position:absolute;left:78px;width:401px;top:120px;text-align:center;font-size:9.2px;line-height:13.3px}
.btn{position:absolute;display:flex;align-items:center;justify-content:center;gap:5px;background:linear-gradient(var(--brand-blue-light),var(--brand-blue));color:var(--white);font-size:7px;font-weight:600;letter-spacing:.2px;border:0}
.btn-video{left:236px;top:182px;width:85px;height:22px;font-family:"Lato",sans-serif}
.slider-dots{position:absolute;left:262px;top:238px;display:flex;gap:5px}
.slider-dots span{width:6px;height:6px;border-radius:50%;background:var(--white)}
.slider-dots span.is-active{background:var(--brand-red)}
.landing-rule{position:absolute;left:35px;width:488px;top:278px;height:1px;background:rgba(255,255,255,.35)}
.copyright{position:absolute;font-family:"Lato",sans-serif;font-size:6px}
.landing .copyright{left:35px;top:293px;color:#cbcbcb}
.social{position:absolute;display:flex;align-items:center;gap:9px}
.social span{width:8px;height:8px;background:currentColor;border-radius:50%}
.social em{font-style:normal;font-family:"Lato",sans-serif;font-size:6.5px;margin-left:1px}
.landing .social{left:445px;top:293px;color:var(--white)}

/* Home screen */
.home{position:absolute;left:609px;top:45px;width:557px;height:474px;background:var(--white);font-family:"Lato",sans-serif;overflow:hidden}
.site-header{position:absolute;left:0;top:0;width:100%;height:46px}
.site-brand{position:absolute;left:35px;top:17px;font-size:14px;font-weight:700;color:var(--ink)}
.site-brand .brand-dot{display:inline-block;width:8px;height:8px;background:var(--brand-red);border-radius:50%;margin-right:4px;vertical-align:1px}
.site-nav a{position:absolute;top:22px;font-size:6.3px;font-weight:700;color:var(--ink);text-decoration:none}
.site-nav a.is-current{color:var(--brand-red)}
.hero{position:absolute;left:0;top:46px;width:100%;height:248px}
.hero-backdrop{position:absolute;inset:0;background:radial-gradient(ellipse at 50% 55%,var(--hero-mid) 0%,#143f6c 45%,var(--hero-dark) 100%)}
.hero-title{position:absolute;left:0;right:0;top:104px;text-align:center;font-family:"Fira Sans",sans-serif;font-size:15px;font-weight:600;line-height:19.5px;color:var(--white)}
.intro{position:absolute;left:74px;width:410px;top:313px;text-align:center;font-size:7px;line-height:11.6px;color:var(--ink)}
.intro p+p{margin-top:8px}
.btn-parcel{left:188px;top:390px;width:84px;height:22px;font-size:7px}
.btn-tech{left:285px;top:390px;width:84px;height:22px;font-size:7px}
.site-footer{position:absolute;left:0;top:440px;width:100%;height:34px;background:var(--footer-grey);color:var(--white)}
.site-footer .copyright{left:35px;top:15px}
.site-footer .social{left:445px;top:14px}
</style>
</head>
<body>
<main class="stage">

  <section class="landing">
    <div class="landing-backdrop" role="img" aria-label="Warehouse interior with digital network overlay"></div>
    <div class="landing-shade"></div>
    <div class="landing-brand"><span class="brand-dot"></span>Brisk. Technology</div>
    <h1 class="landing-title">Brisk.Technology ... Our Focus</h1>
    <p class="landing-copy">We provide advanced software solutions to ensure you connect with global e zcommerce delivery carriers you can manage your Global Delivery Network in one place, with our software will enable you monitor the productivity and reporting of your e commerce deliveries manage your carriers,&nbsp; your delivery speeds, and your costs</p>
    <a class="btn btn-video">
      <svg width="6" height="6" viewBox="0 0 10 10"><circle cx="5" cy="5" r="5" fill="#fff"/><path d="M4 3l3 2-3 2z" fill="#0355a3"/></svg>
      PLAY VIDEO
    </a>
    <div class="slider-dots"><span class="is-active"></span><span></span><span></span><span></span></div>
    <div class="landing-rule"></div>
    <p class="copyright">Copyright © 2018. Company Name.&nbsp; All Right Reserved</p>
    <div class="social"><span></span><span></span><span></span><span></span><span></span><em>x10</em></div>
  </section>

  <section class="home">
    <header class="site-header">
      <div class="site-brand"><span class="brand-dot"></span>Brisk. Technology</div>
      <nav class="site-nav">
        <a class="is-current" style="left:313px">HOME</a>
        <a style="left:351px">SOLUTIONS</a>
        <a style="left:407px">TESTIMONIALS LOGIN</a>
        <a style="left:493px">CONTACT</a>
      </nav>
    </header>
    <div class="hero">
      <div class="hero-backdrop" role="img" aria-label="World map with glowing global delivery routes"></div>
      <h1 class="hero-title">Brisk. Technology and Parcel Solutions Built To Help Develop<br>&amp; Manage Your Global Delivery Network</h1>
    </div>
    <div class="intro">
      <p>Working closely with Ecommerce, Brisk. Technology have developed solutions purely focused on delivering what’s required within the global delivery marketplace. Meeting all needs and more for Retailers and Global Delivery Solution providers allowing customers to grow at a fast pace; most importantly providing tools to help them manage their global delivery network supported by “Dynamic Real Time Visibility” management tools</p>
      <p>Ensuring solutions evolve to suit our customers business requirements.</p>
    </div>
    <a class="btn btn-parcel">BRISK PARCEL</a>
    <a class="btn btn-tech">BRISK TECHNOLOGY</a>
    <footer class="site-footer">
      <p class="copyright">Copyright © 2018. Company Name.&nbsp; All Right Reserved</p>
      <div class="social"><span></span><span></span><span></span><span></span><span></span><em>x10</em></div>
    </footer>
  </section>

</main>
</body>
</html>
```